Crimson Ridge Footrace Co.

We need a website (wordpress) design for a new website that we will be launching. This is for a new trail racing series in Canada.
We recently had a logo designed so want to incorporate the colours of the logo on the website design. Especially the dark blue, green and orange.
Websites that we like for comparison of trail running race themes are:
https://www.mosslinerunning.com/
https://www.bramblestridecup.com/
http://www.quarrypathcircuit.ca/
https://www.cobaltcreekchase.com/
http://www.dunmoorrunningtour.com/

Target Market(s)

Outdoor trail runners

Coding

Coded - Design and coding required

Number of Pages Required

4 page

Font styles to use
Sans Serif

Colors
0255a3
33b8a4
f37122

Requirements
Must have
• There will be a main page with eye catching design noting what we do. Page 2 and 3 will be for each race in the series. Page 1 will be a specific race, and page 2 with be for another race. page 3 and 4 will be for future races that we add so that each race has their own page.
• Our races all take place in the mountains, so using graphics including mountains, rivers, trees is all a requirement for us.
• Our logo is attached, we want to use the colours of the logo in the website design.
Nice to have
• Outdoor theme is a nice to have. We like wood and earth tone colours, and pictures/graphics of runners and mountains and trees.
• There are 4 people involved in our organization. We'd like a photo and brief blurb of each of us, similar to how this website did their layout: https://www.mosslinerunning.com/

```html
<!DOCTYPE html>
<html lang="en">
<head>
<meta charset="utf-8">
<title>Crimson Ridge Footrace Co.</title>
<link href="https://fonts.googleapis.com/css2?family=Raleway:wght@400;500;600;700&family=Open+Sans:wght@400;600&display=swap" rel="stylesheet">
<style>
:root{
  --blue:#0255a3;
  --teal:#33b8a4;
  --orange:#f37122;
  --ink:#3a3f44;
  --muted:#6f767c;
  --mist:#eef1f3;
  --white:#ffffff;
}
*{margin:0;padding:0;box-sizing:border-box}
html,body{width:1200px;height:2856px;overflow:hidden}
body{position:relative;background:var(--white);font-family:"Open Sans",Arial,sans-serif;color:var(--ink)}
.heading{font-family:"Raleway",Arial,sans-serif}

/* Navigation */
.site-nav{position:absolute;top:0;left:0;width:1200px;height:88px;background:var(--white);z-index:3}
.site-nav a{position:absolute;top:32px;font-family:"Raleway",Arial,sans-serif;font-size:18px;font-weight:500;color:var(--ink);text-decoration:none}
.brand-badge{position:absolute;top:-6px;left:492px;width:216px;height:216px;border-radius:50%;background:var(--white);z-index:4;display:flex;align-items:center;justify-content:center;text-align:center;padding:34px;box-shadow:0 4px 14px rgba(0,0,0,.12)}
.brand-name{font-family:"Raleway",Arial,sans-serif;font-weight:700;font-size:25px;line-height:1.2;color:var(--blue)}

/* Hero */
.hero-photo{position:absolute;top:88px;left:72px;width:1056px;height:584px;background:linear-gradient(160deg,#9aa06a 0%,#5d6b3c 35%,#3f4a2a 60%,#8a7556 100%)}
.hero-dots{position:absolute;top:630px;left:0;width:1200px;display:flex;justify-content:center;gap:10px}
.hero-dots span{width:10px;height:10px;border-radius:50%;background:rgba(255,255,255,.6)}
.hero-dots span.active{background:var(--white)}

/* Welcome */
.welcome{position:absolute;top:672px;left:0;width:1200px;height:400px;background:linear-gradient(180deg,#ffffff 0%,#ffffff 55%,#e7ebee 80%,#d9dfe3 100%)}
.welcome-title{position:absolute;top:56px;left:0;width:1200px;text-align:center;font-size:40px;font-weight:500;color:var(--ink)}
.welcome-title strong{font-weight:700}
.welcome-text{position:absolute;top:122px;left:160px;width:880px;text-align:center;font-size:15px;line-height:1.75;color:var(--muted)}
.btn{position:absolute;top:254px;left:525px;width:150px;height:46px;border-radius:23px;background:var(--teal);color:var(--white);font-family:"Raleway",Arial,sans-serif;font-weight:600;font-size:15px;letter-spacing:1px;display:flex;align-items:center;justify-content:center}

/* Events */
.events{position:absolute;top:1072px;left:0;width:1200px;height:560px;background:linear-gradient(180deg,var(--orange) 0%,#ef6a1c 70%,#e26116 100%)}
.section-title{position:absolute;left:0;width:1200px;text-align:center;font-size:40px;font-weight:500}
.events .section-title{top:42px;color:#2b2b2b}
.events .section-title strong{font-weight:700}
.event-photo{position:absolute;top:168px;left:72px;width:528px;height:380px;background:linear-gradient(150deg,#7f9b57 0%,#5f7a3d 45%,#a98a62 100%)}
.event-card{position:absolute;top:152px;left:592px;width:536px;height:304px;background:rgba(120,45,10,.55);border:2px solid rgba(255,255,255,.75);padding:28px 32px;color:var(--white)}
.event-meta{font-size:13px;opacity:.9;margin-bottom:14px}
.event-title{font-family:"Raleway",Arial,sans-serif;font-size:22px;font-weight:700;line-height:1.35;margin-bottom:16px}
.event-text{font-size:14px;line-height:1.65;opacity:.92;margin-bottom:18px}
.event-link{font-size:15px;font-weight:600;text-decoration:underline}
.slider-arrows{position:absolute;top:484px;left:676px;display:flex;gap:22px}

/* Team */
.team{position:absolute;top:1632px;left:0;width:1200px;height:576px;background:var(--teal)}
.team .section-title{top:100px;color:#1f2a2a}
.team-card{position:absolute;top:176px;width:248px;height:272px}
.team-photo{width:100%;height:100%;background:linear-gradient(180deg,#cfd3d6 0%,#8e9398 60%,#3d4247 100%)}
.team-photo.dark{background:linear-gradient(180deg,#6a6e72 0%,#3a3e42 60%,#1f2226 100%)}
.team-label{position:absolute;left:0;bottom:-64px;width:100%;height:68px;background:var(--blue);color:var(--white);text-align:center;padding-top:14px}
.team-label .name{font-family:"Raleway",Arial,sans-serif;font-weight:700;font-size:16px;letter-spacing:1px;text-transform:uppercase}
.team-label .role{font-size:12px;opacity:.85;margin-top:4px}

/* Testimonials */
.testimonials{position:absolute;top:2208px;left:0;width:1200px;height:352px;background:linear-gradient(180deg,#ffffff 0%,#eef1f3 35%,#d8dee2 75%,#eef1f3 100%)}
.testimonials .section-title{top:52px;color:#2b2b2b}
.avatar{position:absolute;top:140px;left:212px;width:110px;height:110px;border-radius:50%;background:linear-gradient(160deg,#c9b7a6,#6a5a4e);border:4px solid var(--white)}
.quote{position:absolute;top:140px;left:352px;width:640px;font-size:15px;line-height:1.7;color:var(--muted);font-style:italic}
.quote-author{position:absolute;top:296px;left:352px;font-size:14px;font-weight:600;color:var(--ink)}
.arrow-side{position:absolute;top:176px}

/* Footer */
.site-footer{position:absolute;top:2560px;left:0;width:1200px;height:296px;background:var(--white)}
.footer-brand{position:absolute;top:70px;left:72px;width:220px;font-family:"Raleway",Arial,sans-serif;font-weight:700;font-size:30px;line-height:1.15;color:var(--blue)}
.footer-heading{position:absolute;top:60px;font-family:"Raleway",Arial,sans-serif;font-size:20px;font-weight:600;color:var(--ink)}
.footer-links{position:absolute;top:104px;list-style:none;font-size:13px;line-height:2;color:var(--muted);text-transform:uppercase}
.newsletter-text{position:absolute;top:100px;left:876px;width:252px;font-size:13px;line-height:1.6;color:var(--muted)}
.newsletter-form{position:absolute;top:156px;left:876px;width:252px;height:40px;display:flex;border:1px solid #d3d8dc}
.newsletter-form .field{flex:1;font-size:12px;color:#9aa1a6;padding:12px 12px}
.newsletter-form .submit{width:40px;background:var(--blue);display:flex;align-items:center;justify-content:center}
.social{position:absolute;top:216px;left:900px;display:flex;gap:14px}
.social span{width:22px;height:22px;border-radius:50%;background:var(--blue)}
.footer-url{position:absolute;top:262px;left:72px;font-size:12px;color:var(--muted)}
</style>
</head>
<body>

<nav class="site-nav">
  <a style="left:112px">Home</a>
  <a style="left:240px">About Us</a>
  <a style="left:400px">Events</a>
  <a style="left:740px">Team</a>
  <a style="left:870px">Blog</a>
  <a style="left:985px">Contact Us</a>
</nav>
<div class="brand-badge"><span class="brand-name">Crimson Ridge Footrace Co.</span></div>

<div class="hero-photo" role="img" aria-label="Trail runners climbing a rocky forest path"></div>
<div class="hero-dots"><span class="active"></span><span></span><span></span><span></span><span></span></div>

<section class="welcome">
  <div role="img" aria-label="Faint mountain range backdrop" style="position:absolute;inset:0"></div>
  <h1 class="welcome-title heading">Welcome to <strong>Crimson Ridge Footrace Co.</strong></h1>
  <p class="welcome-text">Race the high country with us. Our trail series takes runners through alpine ridges, river valleys and old-growth forest across Canada. Every course is marked, supported and built for runners who love the mountains.</p>
  <div class="btn">READ MORE</div>
</section>

<section class="events">
  <h2 class="section-title heading">Our <strong>Events</strong></h2>
  <div class="event-photo" role="img" aria-label="Runners on a trail through green trees"></div>
  <article class="event-card">
    <div class="event-meta">Date: 14 Jun 2025 &nbsp;|&nbsp; By: Race Director</div>
    <h3 class="event-title">Cedar Creek 25K opens registration for the summer season.</h3>
    <p class="event-text">Climb through cedar stands to a river crossing and an open ridge with views of the whole valley. Aid stations every eight kilometres.</p>
    <span class="event-link">Read more</span>
  </article>
  <div class="slider-arrows">
    <svg width="14" height="22" viewBox="0 0 14 22"><path d="M11 3 L3 11 L11 19" fill="none" stroke="#2b2b2b" stroke-width="3"/></svg>
    <svg width="14" height="22" viewBox="0 0 14 22"><path d="M3 3 L11 11 L3 19" fill="none" stroke="#2b2b2b" stroke-width="3"/></svg>
  </div>
</section>

<section class="team">
  <h2 class="section-title heading">Our Team</h2>
  <div class="team-card" style="left:72px"><div class="team-photo" role="img" aria-label="Portrait of a team member"></div></div>
  <div class="team-card" style="left:344px">
    <div class="team-photo dark" role="img" aria-label="Portrait of team member Nolan Reyes"></div>
    <div class="team-label"><div class="name">Nolan Reyes</div><div class="role">Race Director</div></div>
  </div>
  <div class="team-card" style="left:616px"><div class="team-photo" role="img" aria-label="Portrait of a team member"></div></div>
  <div class="team-card" style="left:880px"><div class="team-photo" role="img" aria-label="Portrait of a team member"></div></div>
</section>

<section class="testimonials">
  <div role="img" aria-label="Misty mountain range backdrop" style="position:absolute;inset:0"></div>
  <h2 class="section-title heading">Testimonials</h2>
  <svg class="arrow-side" style="left:148px" width="16" height="26" viewBox="0 0 16 26"><path d="M13 3 L3 13 L13 23" fill="none" stroke="#2b2b2b" stroke-width="3.5"/></svg>
  <div class="avatar" role="img" aria-label="Photo of runner Dale Mercer"></div>
  <p class="quote">“Trail days with this crew are the highlight of my running year. The courses are tough, honest and beautifully marked, and the volunteers at every aid station make you feel at home on the mountain.”</p>
  <div class="quote-author">- Dale Mercer</div>
  <svg class="arrow-side" style="left:1036px" width="16" height="26" viewBox="0 0 16 26"><path d="M3 3 L13 13 L3 23" fill="none" stroke="#2b2b2b" stroke-width="3.5"/></svg>
</section>

<footer class="site-footer">
  <div class="footer-brand">Crimson Ridge Footrace Co.</div>
  <h4 class="footer-heading" style="left:430px">Useful Links</h4>
  <ul class="footer-links" style="left:430px"><li>Home</li><li>About Us</li><li>Events</li><li>Team</li></ul>
  <ul class="footer-links" style="left:590px"><li>Blog</li><li>Testimonials</li><li>Contact Us</li></ul>
  <h4 class="footer-heading" style="left:876px">Newsletter</h4>
  <p class="newsletter-text">Get race news and early entry dates in your inbox.</p>
  <div class="newsletter-form">
    <div class="field">Enter your email address</div>
    <div class="submit"><svg width="16" height="16" viewBox="0 0 16 16"><path d="M1 8 L15 1 L11 15 L8 9 Z" fill="#fff"/></svg></div>
  </div>
  <div class="social"><span></span><span></span><span></span><span></span><span></span></div>
  <div class="footer-url">www.crimsonridgefootrace.ca</div>
</footer>

</body>
</html>
```